Landingpage design

We need a landingpage for a Chatterloom add campaign. We sell socks made of bamboo in super quality. Our customers loves us, and we have a 5 heart rating at scorevane.com.

We want to create a add campaign targeted new customers, and the offer is that they can buy 1 pair of bamboo socks as a test, for only 20 DKK (2,7 Euro) including shipment. Our webpage is www.tuvelo.dk, landingpage should be built i Kyvio, a wysiwyg editor. based on their template. like:
https://tuvelo.pemlorsite.com/13844-sales-page
https://tuvelo.pemlorsite.com/13696-sales-page
https://tuvelo.pemlorsite.com/13845-sales-page

You don't have to follow the templates 100% if you have better ideas. We have an account for snapvaultly, so please get stockphotos from here.

Bamboo socks has a lot of great selling points, you can see a good desciption here:
https://feltrano.com/us/why-bamboo

We expect you to have experience in landingpage design, and expect to end up with 2 landingpages we can splittest on.

This is the first of a number of landingpages we need in the future, so for the right person there will be plenty of more work.

Target Market(s)

Denmark

Industry/Entity Type

E-Commerce

Number of Pages Required

2 page

Colors

Designer to choose colors to be used in the design.

Requirements
Must have
• A great selling page, showing all the great things with bamboo socks. It should be supplied with good packshots from snapvaultly.com

```html
<!DOCTYPE html>
<html lang="en">
<head>
<meta charset="utf-8">
<title>Feltrano – Bamboo Socks</title>
<link href="https://fonts.googleapis.com/css2?family=Roboto:wght@400;500&display=swap" rel="stylesheet">
<style>
:root{
  --green:#3db183;
  --green-top:#39ad80;
  --green-bottom:#3adda1;
  --ink:#555555;
  --ink-soft:#808080;
  --ink-faint:#a0a0a0;
  --hero-bg:#f1f1f1;
  --card-bg:#f2f2f2;
  --white:#ffffff;
}
*{margin:0;padding:0;box-sizing:border-box}
html,body{width:1200px;height:2219px;overflow:hidden;background:var(--white)}
body{position:relative;font-family:"Roboto",Arial,sans-serif;color:var(--ink)}
.abs{position:absolute}

/* header */
.site-header{left:0;top:0;width:1200px;height:70px;background:var(--white)}
.brand{left:135px;top:18px;display:flex;align-items:center;gap:6px;font-size:25px;font-weight:400;color:#1f1f1f;letter-spacing:.3px}
.brand-dot{width:22px;height:22px;border-radius:50%;background:var(--green)}
.nav a{position:absolute;top:26px;font-size:13px;color:#6a6a6a;text-decoration:none;letter-spacing:.3px}
.nav .is-active{border-bottom:1px solid #6a6a6a;padding-bottom:2px}
.btn{display:flex;align-items:center;justify-content:center;font-size:13px;font-weight:500;letter-spacing:.3px;text-transform:uppercase;text-decoration:none}
.btn-solid{background:var(--green);color:var(--white)}
.btn-ghost{border:1px solid var(--green);color:var(--green);gap:12px}
.header-cta{left:908px;top:21px;width:157px;height:28px}

/* hero */
.hero{left:0;top:70px;width:1200px;height:474px;background:var(--hero-bg)}
.hero-title{left:135px;top:176px;font-size:44px;font-weight:500;line-height:52px;color:var(--ink)}
.hero-lead{left:135px;top:298px;width:490px;font-size:17px;line-height:26px;color:var(--ink-soft)}
.hero-buy{left:135px;top:372px;width:193px;height:36px}
.hero-video{left:345px;top:372px;width:193px;height:36px}
.hero-note{left:135px;top:417px;font-size:13px;color:var(--ink-faint)}
.hero-model{left:815px;top:100px;width:250px;height:444px;background:linear-gradient(180deg,#e4e4e4 0%,#d9c2ae 45%,#4f9a62 80%,#3e8a55 100%);border-radius:90px 90px 0 0}

/* why bamboo */
.why{left:0;top:544px;width:1200px;height:513px;background:linear-gradient(180deg,var(--green-top) 0%,var(--green-bottom) 100%)}
.why-title{left:0;top:642px;width:1200px;text-align:center;font-size:35px;font-weight:400;color:var(--white)}
.why-rule{left:546px;top:687px;width:108px;height:2px;background:var(--white)}
.why-text{left:250px;top:703px;width:700px;text-align:center;font-size:16px;font-weight:500;line-height:27px;color:var(--white)}
.benefits{left:135px;top:813px;width:930px;height:138px;display:flex;background:var(--card-bg)}
.benefit{flex:1;padding:26px 18px 0;text-align:center;border-left:1px solid #dcdcdc}
.benefit:first-child{border-left:none}
.benefit h3{font-size:20px;font-weight:400;color:#444;margin-bottom:8px}
.benefit p{font-size:11.5px;line-height:17px;color:var(--ink-faint)}

/* feature rows */
.feature-photo{width:421px;height:245px}
.feature-title{font-size:30px;font-weight:500;color:var(--ink)}
.feature-text{width:460px;font-size:15.5px;line-height:27px;color:var(--ink-soft)}
.photo-shoes{left:135px;top:1172px;background:linear-gradient(135deg,#2d2d2d 0%,#6c6c6c 45%,#8a5a70 60%,#9a9a9a 100%)}
.photo-legs{left:644px;top:1514px;background:linear-gradient(100deg,#1f2733 0%,#2e3a4a 45%,#c9a99a 70%,#3a4656 100%)}
.photo-socks{left:135px;top:1857px;background:linear-gradient(135deg,#5a5d60 0%,#8a8c8e 50%,#d5d2cc 70%,#6a6d70 100%)}
.footer-rule{left:0;top:2216px;width:1200px;height:1px;background:#e6e6e6}
</style>
</head>
<body>

<header class="abs site-header">
  <div class="abs brand"><span class="brand-dot"></span>feltrano.com</div>
  <nav class="nav">
    <a href="#" class="is-active" style="left:485px">HOME</a>
    <a href="#" style="left:565px">WHY BAMBOO</a>
    <a href="#" style="left:696px">ABOUT US</a>
    <a href="#" style="left:799px">REVIEWS</a>
  </nav>
  <a href="#" class="abs btn btn-solid header-cta">Buy now</a>
</header>

<section class="abs hero"></section>
<h1 class="abs hero-title">Enjoy Your First Pair of Bamboo<br>Socks for Only 20 PKK</h1>
<p class="abs hero-lead">Feltrano is a new and inspiring clothing brand which offers you the highest quality products</p>
<a href="#" class="abs btn btn-solid hero-buy">Buy now</a>
<a href="#" class="abs btn btn-ghost hero-video">
  <svg width="11" height="12" viewBox="0 0 11 12"><path d="M0 0L11 6L0 12Z" fill="#3db183"/></svg>
  Watch video
</a>
<p class="abs hero-note">Shipment included</p>
<div class="abs hero-model" role="img" aria-label="Model in green bamboo boxer briefs, arms crossed"></div>

<section class="abs why"></section>
<h2 class="abs why-title">Why Bamboo Clothing?</h2>
<div class="abs why-rule"></div>
<p class="abs why-text">It was only in 2011 that the Qinghe Textile Institute discovered how you can make fabric from bamboo stems. Now bamboo has the potential to become the textile of the future.</p>
<div class="abs benefits">
  <div class="benefit"><h3>Comfortable</h3><p>Bamboo fabric breathes making you comfortable in garments made in this.</p></div>
  <div class="benefit"><h3>Eco-friendly</h3><p>Bamboo is a very fast-growing, tropical forest product, which does not require the use of pesticides</p></div>
  <div class="benefit"><h3>Exquistely soft</h3><p>The moment you wear it next to your skin you will notice the difference between other fabrics.</p></div>
  <div class="benefit"><h3>Thermo-control</h3><p>Bamboo fabric is warm, thanks to its hollow microfibre, yet is also breathable.</p></div>
</div>

<div class="abs feature-photo photo-shoes" role="img" aria-label="Grey argyle bamboo socks beside black leather shoes"></div>
<h2 class="abs feature-title" style="left:608px;top:1215px">Strong Material</h2>
<p class="abs feature-text" style="left:609px;top:1265px">Bamboo fabric is lightweight yet strong. The natural processing of verdax bamboo allows the fibre to remain strong to produce an extremely high quality product. This process gives a material that is very durable.</p>

<h2 class="abs feature-title" style="left:133px;top:1557px">Completely Clean</h2>
<p class="abs feature-text" style="left:134px;top:1608px;width:455px">Bamboo fibers doesnot under go much chemical processing to make the fabric ; so you can easily wear it without causing any allergic irritation to the skin that is more prevalent with heavily processes fabrics.</p>
<div class="abs feature-photo photo-legs" role="img" aria-label="Seated person in dark shirt resting a hand on bare legs"></div>

<div class="abs feature-photo photo-socks" role="img" aria-label="Pair of light grey ribbed bamboo socks on a slate surface"></div>
<h2 class="abs feature-title" style="left:608px;top:1913px">Water Absorbent</h2>
<p class="abs feature-text" style="left:609px;top:1963px">Bamboo fibers are water absobent. So if you live in a humid environment this is the fabric for you. Think of the sweat it will absorb and evaporate out of your body.</p>

<div class="abs footer-rule"></div>
</body>
</html>
```